Design 4 pages for an event discovery website

This is a contest for the design of 4 pages for an events discovery website. The feature is part of the new sign-up process.

Please see the attached document for a full scope, mockups and the parent category icons.

Target Market(s)

18-35 Australian event goers

Industry/Entity Type

Events

Number of Pages Required

4 page

```html
<!DOCTYPE html>
<html lang="en">
<head>
<meta charset="utf-8">
<title>gigwave – Sign Up</title>
<link rel="stylesheet" href="https://fonts.googleapis.com/css2?family=Lato:ital,wght@0,300;0,400;0,700;1,400&display=swap">
<style>
  :root {
    --bar-bg: #e9e9e9;
    --brand-green: #0f9d78;
    --lime: #9bc22a;
    --ink: #222222;
    --muted: #9a9a9a;
    --white: #ffffff;
    --social-top: #3c67b6;
    --social-bottom: #1f4596;
    --social-edge: #5b82cf;
    --panel: rgba(0, 0, 0, 0.86);
  }
  * { box-sizing: border-box; margin: 0; padding: 0; }
  html, body { width: 1200px; height: 603px; overflow: hidden; }
  body { font-family: "Lato", sans-serif; color: var(--ink); background: var(--bar-bg); position: relative; }

  .site-header { position: absolute; left: 0; top: 0; width: 1200px; height: 81px; background: var(--bar-bg); }
  .brand { position: absolute; left: 110px; top: 19px; font-size: 36px; font-weight: 700; color: var(--brand-green); letter-spacing: 0.5px; line-height: 1; }
  .nav-link { position: absolute; left: 383px; top: 32px; font-size: 14px; color: var(--ink); text-decoration: none; }
  .search { position: absolute; left: 608px; top: 22px; width: 262px; height: 35px; background: var(--white); border-radius: 9px; }
  .search-placeholder { position: absolute; left: 10px; top: 10px; font-size: 13px; font-style: italic; color: var(--muted); }
  .search-icon { position: absolute; right: 10px; top: 10px; }
  .btn { position: absolute; top: 22px; width: 100px; height: 35px; border-radius: 9px; color: var(--white); font-size: 16px; font-style: italic; text-align: center; line-height: 35px; }
  .btn-signup { left: 881px; background: var(--brand-green); }
  .btn-login { left: 990px; background: var(--lime); }

  .hero { position: absolute; left: 0; top: 81px; width: 1200px; height: 444px; background:
      radial-gradient(ellipse at 75% 30%, rgba(150,110,50,0.55), transparent 55%),
      radial-gradient(ellipse at 20% 60%, rgba(90,60,40,0.5), transparent 60%),
      linear-gradient(180deg, #2a2019 0%, #1c1512 60%, #120e0c 100%); }

  .signup-col { position: absolute; left: 206px; top: 212px; width: 351px; text-align: center; color: var(--white); }
  .signup-title { font-size: 27px; font-weight: 700; line-height: 1; }
  .social-btn { position: relative; margin-top: 14px; height: 71px; border-radius: 10px; background: linear-gradient(180deg, var(--social-top), var(--social-bottom)); box-shadow: 0 4px 0 var(--social-edge), 0 8px 10px rgba(0,0,0,0.4); }
  .social-btn .divider { position: absolute; left: 62px; top: 0; width: 1px; height: 100%; background: rgba(0,0,0,0.25); }
  .social-btn .mark { position: absolute; left: 24px; top: 27px; width: 14px; height: 14px; background: var(--white); }
  .social-btn .label { position: absolute; left: 62px; right: 0; top: 0; line-height: 68px; font-size: 26px; font-weight: 700; }
  .or { margin-top: 42px; font-size: 27px; font-weight: 700; line-height: 1; }
  .alt-link { margin-top: 10px; font-size: 20.5px; line-height: 1.2; white-space: nowrap; }

  .benefits { position: absolute; left: 626px; top: 212px; width: 463px; height: 249px; background: var(--panel); border-radius: 9px; padding: 23px 0 0 25px; color: var(--white); }
  .benefits h2 { font-size: 20.5px; font-weight: 400; color: var(--lime); line-height: 1; margin-bottom: 12px; }
  .benefits ul { list-style: none; }
  .benefits li { position: relative; padding-left: 20px; font-size: 11.3px; font-weight: 300; height: 29px; line-height: 14px; }
  .benefits li svg { position: absolute; left: 2px; top: 3px; }

  .site-footer { position: absolute; left: 0; top: 525px; width: 1200px; height: 78px; background: var(--bar-bg); font-size: 11.5px; color: var(--ink); }
  .copyright { position: absolute; left: 0; width: 100%; top: 32px; text-align: center; }
  .page-code { position: absolute; right: 29px; top: 32px; }
</style>
</head>
<body>
  <header class="site-header">
    <div class="brand">gigwave</div>
    <a class="nav-link" href="#">Find Events</a>
    <div class="search">
      <span class="search-placeholder">Search</span>
      <svg class="search-icon" width="13" height="13" viewBox="0 0 13 13"><circle cx="5.3" cy="5.3" r="4" fill="none" stroke="#555" stroke-width="2"/><line x1="8.3" y1="8.3" x2="12" y2="12" stroke="#555" stroke-width="2.2" stroke-linecap="round"/></svg>
    </div>
    <div class="btn btn-signup">Sign Up</div>
    <div class="btn btn-login">Login</div>
  </header>

  <section class="hero" role="img" aria-label="Concert crowd with raised hands in front of stage lights"></section>

  <div class="signup-col">
    <div class="signup-title">Sign Up</div>
    <div class="social-btn">
      <span class="mark"></span>
      <span class="divider"></span>
      <span class="label">Find Us On Socialnet</span>
    </div>
    <div class="or">Or</div>
    <div class="alt-link">Click here to sign up without &nbsp;Socialnet</div>
  </div>

  <aside class="benefits">
    <h2>The benefits should be listed as</h2>
    <ul>
      <li><svg width="7" height="9" viewBox="0 0 7 9"><polyline points="1.5,1 5.5,4.5 1.5,8" fill="none" stroke="#fff" stroke-width="2"/></svg>Get personalised event recommendations</li>
      <li><svg width="7" height="9" viewBox="0 0 7 9"><polyline points="1.5,1 5.5,4.5 1.5,8" fill="none" stroke="#fff" stroke-width="2"/></svg>Get notified about your favourite events - never miss out again</li>
      <li><svg width="7" height="9" viewBox="0 0 7 9"><polyline points="1.5,1 5.5,4.5 1.5,8" fill="none" stroke="#fff" stroke-width="2"/></svg>Follow all your favourite artists, musicians, teams and players in one place</li>
      <li><svg width="7" height="9" viewBox="0 0 7 9"><polyline points="1.5,1 5.5,4.5 1.5,8" fill="none" stroke="#fff" stroke-width="2"/></svg>Follow your favourite local venues to know everything happening there</li>
      <li><svg width="7" height="9" viewBox="0 0 7 9"><polyline points="1.5,1 5.5,4.5 1.5,8" fill="none" stroke="#fff" stroke-width="2"/></svg>Get curated news and feature content on your favourite artists (coming soon)</li>
      <li><svg width="7" height="9" viewBox="0 0 7 9"><polyline points="1.5,1 5.5,4.5 1.5,8" fill="none" stroke="#fff" stroke-width="2"/></svg>Invite your mates to events via Socialnet (SN sign-up only)</li>
    </ul>
  </aside>

  <footer class="site-footer">
    <div class="copyright">© 2015 Company &nbsp;Name , All Rights Reserved</div>
    <div class="page-code">C5</div>
  </footer>
</body>
</html>
```